Brightfen Business Card Redesign & Logo Update

We need to update our business cards to something more modern and fresh. Brightfen can provide the current color schemes and old design examples, but welcome creativity in helping us with this redesign. PLEASE NOTE that we no longer utilize the "tree" and/or "leaf" imagery in our branding. If able would apprecaite an update on the quality of our "words only" logo in Ai. / PNG formats too.

Target Market(s)

Investors, landowners, corporate partners, contractors

Industry/Entity Type

Environmental Restoration & Conservation

Contact Information for Business Card

Logo, persons name, title, mailing address, phone and email, website url

Font styles to use
Other font styles liked:
• Merriweather

Requirements
Nice to have
• Logo, persons name, title, mailing address, phone and email, website url, but open to ideams
Should not have
• No all back backgrounds

```html
<!DOCTYPE html>
<html lang="en">
<head>
<meta charset="utf-8">
<title>Brightfen Business Card</title>
<link href="https://fonts.googleapis.com/css2?family=Bebas+Neue&family=Oswald:wght@600&family=Open+Sans:wght@400;700&display=swap" rel="stylesheet">
<style>
  :root {
    --stage: #3a3b40;
    --card: #222227;
    --orange: #ee8022;
    --green: #137d3e;
    --white: #ffffff;
  }
  * { box-sizing: border-box; margin: 0; padding: 0; }
  html, body { width: 1200px; height: 780px; overflow: hidden; }
  body {
    background: var(--stage);
    font-family: "Open Sans", sans-serif;
    display: flex;
    align-items: center;
    justify-content: center;
    gap: 40px;
  }
  .card {
    position: relative;
    width: 550px;
    height: 314px;
    background: var(--card);
    overflow: hidden;
    box-shadow: 0 10px 30px rgba(0,0,0,.4);
  }
  .wordmark {
    font-family: "Bebas Neue", sans-serif;
    color: var(--green);
    line-height: .85;
    letter-spacing: 2px;
  }
  .tagline {
    font-family: "Oswald", sans-serif;
    font-weight: 600;
    color: var(--white);
    text-transform: uppercase;
    letter-spacing: .5px;
    line-height: 1;
  }
  /* Front */
  .card-front .brand {
    position: absolute;
    left: 0; right: 0; top: 70px;
    text-align: center;
  }
  .card-front .wordmark { font-size: 118px; }
  .card-front .tagline { font-size: 25px; margin-top: 6px; }
  .card-front .stripes {
    position: absolute; left: 0; bottom: 0; width: 100%;
  }
  .stripe-orange { height: 8px; background: var(--orange); }
  .stripe-gap { height: 3px; background: var(--card); }
  .stripe-green { height: 20px; background: var(--green); }
  /* Back */
  .card-back .swoosh { position: absolute; inset: 0; }
  .card-back .content {
    position: absolute;
    left: 0; right: 0; top: 26px;
    text-align: center;
    color: var(--white);
  }
  .card-back .wordmark { font-size: 64px; }
  .card-back .tagline { font-size: 14px; margin-top: 3px; }
  .person-name {
    margin-top: 16px;
    font-weight: 700;
    font-size: 20px;
    line-height: 1.1;
  }
  .person-name .first { color: var(--orange); }
  .person-name .last { color: var(--green); }
  .person-title { font-size: 12px; margin-top: 2px; }
  .contact-icons {
    display: flex; justify-content: center; gap: 6px;
    margin-top: 8px;
  }
  .contact-icons svg { width: 22px; height: 22px; }
  .contact-lines { margin-top: 6px; font-size: 12.5px; line-height: 1.4; }
</style>
</head>
<body>

<section class="card card-front" aria-label="Business card front">
  <div class="brand">
    <div class="wordmark">BRIGHTFEN</div>
    <div class="tagline">Environmental Credit Company</div>
  </div>
  <div class="stripes">
    <div class="stripe-orange"></div>
    <div class="stripe-gap"></div>
    <div class="stripe-green"></div>
  </div>
</section>

<section class="card card-back" aria-label="Business card back">
  <svg class="swoosh" viewBox="0 0 550 314" preserveAspectRatio="none" aria-hidden="true">
    <path d="M150 314 Q380 285 550 128 L550 314 Z" fill="var(--orange)"/>
    <path d="M0 292 Q340 286 550 168 L550 314 L0 314 Z" fill="var(--green)"/>
  </svg>
  <div class="content">
    <div class="wordmark">BRIGHTFEN</div>
    <div class="tagline">Environmental Credit Company</div>
    <div class="person-name"><span class="first">Lenka</span> <span class="last">Havlova</span></div>
    <div class="person-title">Managing Director</div>
    <div class="contact-icons">
      <svg viewBox="0 0 24 24" aria-label="Phone">
        <circle cx="12" cy="12" r="10.5" fill="none" stroke="var(--orange)" stroke-width="1.6"/>
        <path d="M8.5 7.5 L10.3 7.2 L11 9.6 L10 10.4 Q11 12.9 13.6 14 L14.4 13 L16.8 13.7 L16.5 15.5 Q11 16.5 8.5 7.5 Z" fill="var(--orange)"/>
      </svg>
      <svg viewBox="0 0 24 24" aria-label="Email">
        <circle cx="12" cy="12" r="10.5" fill="none" stroke="var(--orange)" stroke-width="1.6"/>
        <rect x="6.5" y="8.5" width="11" height="7.5" fill="var(--orange)"/>
        <path d="M6.5 8.5 L12 13 L17.5 8.5" fill="none" stroke="var(--card)" stroke-width="1.2"/>
      </svg>
      <svg viewBox="0 0 24 24" aria-label="Website">
        <circle cx="12" cy="12" r="10.5" fill="none" stroke="var(--orange)" stroke-width="1.6"/>
        <circle cx="12" cy="12" r="5.5" fill="none" stroke="var(--orange)" stroke-width="1.3"/>
        <path d="M6.5 12 H17.5 M12 6.5 Q9 12 12 17.5 M12 6.5 Q15 12 12 17.5" fill="none" stroke="var(--orange)" stroke-width="1.1"/>
      </svg>
    </div>
    <div class="contact-lines">
      <div>(555) 014-2286</div>
      <div>info@brightfen.com</div>
      <div>www.brightfen.com</div>
    </div>
  </div>
</section>

</body>
</html>
```